Oriel Photography Business Card

I need a business card designed for a photography business based in Perth, Western Australia called Oriel Photography.

We specialise in wedding, event photography and portrait photography.

The business card must borrow the style of the attached logo.

The hex codes for the colours in the logo are:
#ED1D85 - Pink
#89C23E - Green
#37282F - Black

The name on the card will be:
Name: Tobrian
Phone: 0417395268
Website: www.orielphotography.example.com.au
Facebook: orielphotography

I am open and happy to accept creative concepts.

I’d like some space at the back for writing notes and appointment details.

```html
<!DOCTYPE html>
<html lang="en">
<head>
<meta charset="utf-8">
<title>Oriel Photography – Business Card</title>
<link rel="stylesheet" href="https://fonts.googleapis.com/css2?family=Didact+Gothic&family=Open+Sans:wght@400;700&display=swap">
<style>
  :root {
    --pink: #ED1D85;
    --green: #89C23E;
    --ink: #37282F;
    --paper: #FFFFFF;
    --backdrop: #EEEBE7;
    --rule: #9A9497;
  }
  * { box-sizing: border-box; margin: 0; padding: 0; }
  html, body { width: 1200px; height: 720px; overflow: hidden; }
  body {
    background: var(--backdrop);
    font-family: "Didact Gothic", "Century Gothic", sans-serif;
    color: var(--ink);
    position: relative;
  }
  .card {
    position: absolute;
    top: 211px;
    width: 520px;
    height: 297px;
    background: var(--paper);
    box-shadow: 0 2px 10px rgba(55, 40, 47, 0.18);
    overflow: hidden;
  }
  .card--front { left: 60px; }
  .card--back { left: 620px; }

  .brand {
    position: absolute;
    left: 0; right: 0;
    display: flex;
    flex-direction: column;
    align-items: center;
    z-index: 1;
  }
  .brand__mark {
    width: 40px; height: 40px;
    border-radius: 50%;
    background: var(--pink);
  }
  .brand__name {
    margin-top: 10px;
    font-size: 13px;
    letter-spacing: 0.52em;
    text-transform: uppercase;
    padding-left: 0.52em;
    color: var(--ink);
  }
  .card--front .brand { top: 20px; }
  .card--back .brand { top: 30px; }

  .contact {
    position: absolute;
    top: 106px;
    left: 0; right: 0;
    display: flex;
    flex-direction: column;
    align-items: center;
    gap: 5px;
    font-family: "Open Sans", sans-serif;
    font-size: 11.5px;
    color: var(--ink);
    z-index: 1;
  }
  .contact__row { display: flex; gap: 14px; align-items: center; }
  .contact__item { display: flex; align-items: center; gap: 5px; }
  .contact__icon { width: 11px; height: 11px; flex: none; }
  .contact__square {
    width: 10px; height: 10px;
    background: var(--ink);
    flex: none;
  }

  .wave { position: absolute; inset: 0; width: 520px; height: 297px; }
  .holder-name {
    position: absolute;
    left: 34px;
    top: 238px;
    font-family: "Open Sans", sans-serif;
    font-weight: 700;
    font-size: 16px;
    letter-spacing: 0.04em;
    color: var(--paper);
    text-transform: uppercase;
  }

  .notes {
    position: absolute;
    left: 26px; right: 26px;
    top: 100px;
  }
  .notes__line {
    height: 26px;
    border-bottom: 1px dotted var(--rule);
    display: flex;
    align-items: flex-end;
  }
  .notes__line:first-child { margin-left: 150px; }
  .notes__line:nth-child(2) { margin-left: 110px; }
  .notes__label {
    font-family: "Open Sans", sans-serif;
    font-size: 15px;
    line-height: 1;
    padding-bottom: 2px;
    color: var(--ink);
  }
  .back-web {
    position: absolute;
    left: 0; right: 0;
    bottom: 18px;
    text-align: center;
    font-size: 13px;
    letter-spacing: 0.08em;
    color: var(--ink);
  }
</style>
</head>
<body>

<section class="card card--front" aria-label="Business card front">
  <svg class="wave" viewBox="0 0 520 297" aria-hidden="true">
    <path d="M0 297 L0 222 C160 196 330 214 520 140 L520 297 Z" fill="#ED1D85"/>
    <path d="M0 214 C160 188 330 206 520 132" fill="none" stroke="#89C23E" stroke-width="5"/>
    <path d="M0 204 C165 176 335 194 520 121" fill="none" stroke="#89C23E" stroke-width="2"/>
  </svg>

  <div class="brand">
    <span class="brand__mark" aria-hidden="true"></span>
    <span class="brand__name">Oriel Photography</span>
  </div>

  <div class="contact">
    <div class="contact__row">
      <span class="contact__item">
        <svg class="contact__icon" viewBox="0 0 12 12" aria-hidden="true">
          <circle cx="6" cy="6" r="6" fill="#89C23E"/>
          <path d="M4 3.2 L5 3 L5.6 4.6 L5 5.2 C5.4 6 6 6.6 6.8 7 L7.4 6.4 L9 7 L8.8 8 C6.2 8.4 3.6 5.8 4 3.2Z" fill="#fff"/>
        </svg>
        0417395268
      </span>
      <span class="contact__item">
        <span class="contact__square" aria-hidden="true"></span>
        orielphotography
      </span>
    </div>
    <span class="contact__item">
      <svg class="contact__icon" viewBox="0 0 12 12" aria-hidden="true">
        <circle cx="6" cy="6" r="6" fill="#89C23E"/>
        <circle cx="6" cy="6" r="3.4" fill="none" stroke="#fff" stroke-width="0.9"/>
        <line x1="2.6" y1="6" x2="9.4" y2="6" stroke="#fff" stroke-width="0.9"/>
        <ellipse cx="6" cy="6" rx="1.4" ry="3.4" fill="none" stroke="#fff" stroke-width="0.9"/>
      </svg>
      www.orielphotography.example.com.au
    </span>
  </div>

  <span class="holder-name">Tobrian</span>
</section>

<section class="card card--back" aria-label="Business card back">
  <div class="brand">
    <span class="brand__mark" aria-hidden="true"></span>
    <span class="brand__name">Oriel Photography</span>
  </div>

  <div class="notes">
    <div class="notes__line"></div>
    <div class="notes__line"></div>
    <div class="notes__line"><span class="notes__label">notes:</span></div>
    <div class="notes__line"></div>
    <div class="notes__line"></div>
  </div>

  <p class="back-web">www.orielphotography.example.com.au</p>
</section>

</body>
</html>
```